RWT Fittings Ltd Business Cards

We need a business card with our business logo. We provide window and door installations on high-rises in west coast British Colombia, Canada.

I would like my business information and details on one side of the card, and the other side the company name with logo

Target Market(s)

General Contractors

Industry/Entity Type

Construction

Contact Information for Business Card

one side i want my company name and logo in the dark theme logo that i provided

Requirements
Must have
• Marco Peltieri, 16045518293, RWTFittings@mailbox-demo.com, 1407-5194 Linden Row Burnaby BC, V5H 2K9, Owner & Manager

```html
<!DOCTYPE html>
<html lang="en">
<head>
<meta charset="UTF-8">
<title>RWT Fittings Ltd — Business Cards</title>
<link rel="stylesheet" href="https://fonts.googleapis.com/css2?family=Open+Sans:wght@400;600;700&display=swap">
<style>
  :root {
    --stage-top: #5a5a5a;
    --stage-bottom: #141414;
    --card: #1a1a1a;
    --card-pattern: #121212;
    --accent: #29a8e0;
    --text: #e6e6e6;
    --text-soft: #bdbdbd;
  }
  * { box-sizing: border-box; margin: 0; padding: 0; }
  html, body {
    width: 1200px;
    height: 780px;
    overflow: hidden;
  }
  body {
    background: linear-gradient(135deg, var(--stage-top) 0%, #2e2e2e 50%, var(--stage-bottom) 100%);
    font-family: "Open Sans", Arial, sans-serif;
    display: flex;
    align-items: center;
    justify-content: center;
    gap: 40px;
  }
  .card {
    position: relative;
    width: 560px;
    height: 320px;
    background: var(--card);
    box-shadow: 0 18px 40px rgba(0, 0, 0, 0.55);
    overflow: hidden;
  }

  /* Front: contact details */
  .contact {
    position: absolute;
    left: 44px;
    top: 40px;
  }
  .contact__name {
    position: relative;
    padding-left: 22px;
    color: var(--accent);
    font-weight: 700;
    font-size: 21px;
    letter-spacing: 0.5px;
    text-transform: uppercase;
    line-height: 1.2;
  }
  .contact__name::before {
    content: "";
    position: absolute;
    left: 0;
    top: 2px;
    width: 10px;
    height: 24px;
    background: var(--accent);
  }
  .contact__role {
    padding-left: 22px;
    color: var(--text);
    font-size: 13.5px;
    margin-top: 2px;
  }
  .contact__address {
    font-style: normal;
    color: var(--text);
    font-size: 13px;
    line-height: 1.45;
    margin-top: 14px;
    padding-left: 22px;
  }
  .contact__list {
    list-style: none;
    margin-top: 12px;
    padding-left: 4px;
  }
  .contact__item {
    display: flex;
    align-items: center;
    gap: 8px;
    color: var(--text);
    font-size: 13px;
    line-height: 1.7;
  }
  .contact__icon {
    width: 11px;
    height: 11px;
    flex: none;
    fill: var(--accent);
  }

  .brand {
    position: absolute;
    display: flex;
    align-items: center;
    gap: 12px;
  }
  .brand__mark {
    background: var(--accent);
    flex: none;
  }
  .brand__name {
    color: var(--accent);
    font-weight: 700;
    white-space: nowrap;
  }
  .brand--front {
    right: 36px;
    bottom: 46px;
  }
  .brand--front .brand__mark { width: 30px; height: 30px; }
  .brand--front .brand__name { font-size: 30px; }

  /* Back: company name over dark texture */
  .card__texture {
    position: absolute;
    inset: 0;
    background: linear-gradient(160deg, #1c1c1c 0%, var(--card-pattern) 100%);
  }
  .brand--back {
    left: 50%;
    top: 50%;
    transform: translate(-50%, -50%);
  }
  .brand--back .brand__mark { width: 22px; height: 22px; }
  .brand--back .brand__name { font-size: 24px; }
</style>
</head>
<body>

  <section class="card card--front" aria-label="Business card front">
    <div class="contact">
      <h1 class="contact__name">Marco Peltieri</h1>
      <p class="contact__role">Owner &amp; Manager</p>
      <address class="contact__address">
        1407-5194 Linden Row<br>
        Burnaby BC, V5H 2K9
      </address>
      <ul class="contact__list">
        <li class="contact__item">
          <svg class="contact__icon" viewBox="0 0 24 24" aria-hidden="true"><path d="M6.6 10.8a15.1 15.1 0 0 0 6.6 6.6l2.2-2.2a1 1 0 0 1 1-.25 11.4 11.4 0 0 0 3.6.57 1 1 0 0 1 1 1V20a1 1 0 0 1-1 1A17 17 0 0 1 3 4a1 1 0 0 1 1-1h3.5a1 1 0 0 1 1 1c0 1.25.2 2.45.57 3.57a1 1 0 0 1-.25 1z"/></svg>
          16045518293
        </li>
        <li class="contact__item">
          <svg class="contact__icon" viewBox="0 0 24 24" aria-hidden="true"><path d="M2 5h20v14H2zm2 2v.5l8 5 8-5V7l-8 5z"/></svg>
          RWTFittings@mailbox-demo.com
        </li>
        <li class="contact__item">
          <svg class="contact__icon" viewBox="0 0 24 24" aria-hidden="true"><path d="M12 2a10 10 0 1 0 0 20 10 10 0 0 0 0-20zm6.9 6h-2.9a15.6 15.6 0 0 0-1.4-3.6A8 8 0 0 1 18.9 8zM12 4c.8 1.2 1.5 2.5 1.9 4h-3.8c.4-1.5 1.1-2.8 1.9-4zM4.3 14a8 8 0 0 1 0-4h3.4a16 16 0 0 0 0 4zm.8 2h2.9c.3 1.3.8 2.5 1.4 3.6A8 8 0 0 1 5.1 16zM8 8H5.1a8 8 0 0 1 4.3-3.6C8.8 5.5 8.3 6.7 8 8zm4 12c-.8-1.2-1.5-2.5-1.9-4h3.8c-.4 1.5-1.1 2.8-1.9 4zm2.3-6H9.7a14 14 0 0 1 0-4h4.6a14 14 0 0 1 0 4zm.3 5.6c.6-1.1 1.1-2.3 1.4-3.6h2.9a8 8 0 0 1-4.3 3.6zm1.7-5.6a16 16 0 0 0 0-4h3.4a8 8 0 0 1 0 4z"/></svg>
          www.rwtfittings-demo.com
        </li>
      </ul>
    </div>

    <div class="brand brand--front">
      <span class="brand__mark" aria-hidden="true"></span>
      <span class="brand__name">RWT Fittings Ltd</span>
    </div>
  </section>

  <section class="card card--back" aria-label="Business card back">
    <div class="card__texture" role="img" aria-label="Dark repeating texture of building outlines across the card"></div>
    <div class="brand brand--back">
      <span class="brand__mark" aria-hidden="true"></span>
      <span class="brand__name">RWT Fittings Ltd</span>
    </div>
  </section>

</body>
</html>
```